AMBER AND SLATE WEB

We need a home design in wordpress, we have now a web but we would like to improve it. Our current web is www.amberandslatevillas.example Our business is holliday rental of villas in Ibiza. Our guest must know that we are a reliable company, professional and with experience and good reviews. We want them to click in our reservation engine: https://bookings.amberandslatevillas.example/en/ and make reservation in our website. We would also like to say that all the properties that we have are just us who commercialize so we have best price available. Many people are going to see our villas in staylist.example and look to our website to make a reservation with us so we need to show them that they are at the right place and click at our link to our reservation engine. What make us special is that we are a local company, we are from Ibiza, Our guests are always received in person by the Amber and Slate Ibiza team. You will enjoy extensive tourist information when you check in and during the entire stay. You will be attended by ChatterLine and calls, always happy to help so that you have a happy and fun stay! Our guest stay is better than in hotel as they have more spece, private swiming pool, private garden, barbeque ... To rent a villa is the best way to stay in Ibiza. We also have a promotional video: https://vidshare.example/Qm7TzR2pLxA Let our philosophy be shown, we think that coming on holiday to Ibiza implies seeing the nature that we have in Ibiza, hence our name AMBER AND SLATE, like the pins that almost touch the sea in Ibiza, or the posidonea meadows where the intense green of the seaweed and the blue of the sea. We are aware of the environment, and we love Ibiza. For us, the client who visits Ibiza, should rent a car, go around the island, eat in a restaurant one day in front of the sea, is a night of partying to the discs, go shopping, visit the ancient heritage of Umanity, make some aquatic sport, enjoy the pool, those are for us Ibiza.

Target Market(s)

Europe, people from Holand, UK, Germany, France, Spain ...

Industry/Entity Type

Tourism

Colors

Designer to choose colors to be used in the design.

Requirements
Must have
• Pictures of Ibiza.
Nice to have
• Our name Amber and Slate Ibiza is beacuse in Ibiza there is forest that almost touch the watter of the Mediterranean sea, so you can see green of the forest and blue of the sea and the sky. And also beacause under the watter of the sea there is a plant called Posidonia that is also green please see the picture of posidonia.

```html
<!DOCTYPE html>
<html lang="en">
<head>
<meta charset="utf-8">
<title>Amber and Slate Villas Ibiza</title>
<link rel="stylesheet" href="https://fonts.googleapis.com/css2?family=Cinzel:wght@600;700&family=Open+Sans:wght@400;600&family=Montserrat:wght@500;600&display=swap">
<style>
:root{
  --lime:#8fb82a;
  --lime-dark:#7fa521;
  --teal:#1d8d97;
  --teal-title:#1e8ea3;
  --olive:#5e7d22;
  --ink:#333;
  --body:#4a4a4a;
  --sky:#1f4fd0;
  --sea:#1aa0cf;
  --white:#fff;
}
*{margin:0;padding:0;box-sizing:border-box}
html,body{width:1200px;height:2897px;overflow:hidden;background:var(--white)}
body{position:relative;font-family:'Open Sans',sans-serif;color:var(--ink)}
.abs{position:absolute}
.serif{font-family:'Cinzel',serif;font-weight:700}

/* header */
.brand{left:155px;top:36px;display:flex;align-items:center;gap:12px}
.brand-dot{width:34px;height:34px;border-radius:50%;background:var(--lime)}
.brand-name{font-family:'Cinzel',serif;font-weight:600;font-size:24px;color:var(--teal);letter-spacing:.5px}
.main-nav{left:492px;top:40px;display:flex;gap:25px;font-family:'Montserrat',sans-serif;font-weight:600;font-size:15px;color:#333}

/* hero */
.hero-title{left:0;width:1200px;top:294px;text-align:center;color:var(--white);font-size:45px;text-shadow:0 2px 6px rgba(0,0,0,.35)}
.hero-sub{left:0;width:1200px;top:348px;text-align:center;color:var(--white);font-size:31px;text-shadow:0 2px 6px rgba(0,0,0,.35)}
.slide-arrow{width:60px;height:60px;border-radius:50%;background:rgba(255,255,255,.45);display:flex;align-items:center;justify-content:center}
.booking-bar{left:204px;top:421px;width:821px;height:75px;background:#2b9ccf;border-radius:4px}
.field{top:14px;height:45px;background:var(--white);display:flex;align-items:center;justify-content:space-between;padding:0 16px;font-size:15px;color:#444}
.book-btn{top:13px;left:700px;width:104px;height:45px;background:var(--lime);color:var(--white);display:flex;align-items:center;justify-content:center;font-family:'Cinzel',serif;font-weight:700;font-size:16px}

/* welcome */
.video{left:138px;top:845px;width:437px;height:281px;background:linear-gradient(135deg,#8a8478,#c7a38d 55%,#6f7a7c)}
.play{left:185px;top:108px;width:66px;height:66px;border-radius:50%;background:var(--white);display:flex;align-items:center;justify-content:center}
.welcome-title{left:621px;top:842px;font-size:36px;line-height:43px;color:var(--teal-title)}
.welcome-title span{color:var(--olive)}
.welcome-text{left:625px;top:942px;width:455px;font-size:16px;line-height:23.3px;color:var(--body)}
.btn{display:flex;align-items:center;justify-content:center;background:var(--lime);color:var(--white);font-family:'Cinzel',serif;font-weight:700;font-size:16px}
.welcome-btn{left:625px;top:1081px;width:150px;height:45px}

/* why */
.why-title{left:0;width:1165px;top:1280px;text-align:center;color:var(--white);font-size:29px}
.reason{width:280px;text-align:center;color:var(--white);font-family:'Cinzel',serif;font-weight:700;font-size:21px;line-height:23px}
.reason svg{display:block;margin:0 auto 14px}

/* testimonials */
.testi-title{left:0;width:1200px;top:1927px;text-align:center;color:var(--olive);font-size:32px}
.avatar{left:233px;top:2001px;width:162px;height:162px;border-radius:50%;border:2px solid #ddd;background:radial-gradient(circle at 50% 40%,#d7b9a0,#8a6c58 70%,#c8c0c0)}
.quote{left:447px;top:2000px;width:570px;font-size:15.5px;line-height:27px;color:var(--body)}
.quote-mark{font-family:'Cinzel',serif;font-size:46px;color:var(--teal);font-style:normal;line-height:0}
.author{left:447px;top:2145px;font-size:17px;font-weight:600;color:#333}

/* experience */
.exp-title{left:183px;top:2352px;color:var(--white);font-size:35px}
.exp-text{left:180px;top:2412px;width:440px;font-size:16.5px;line-height:25.2px;color:#e9f7fb}
.exp-btn{left:178px;top:2592px;width:163px;height:48px}

/* footer */
.foot-nav{left:172px;top:2797px;display:flex;gap:25px;font-family:'Montserrat',sans-serif;font-weight:600;font-size:15px;color:#222}
.copyright{left:172px;top:2828px;font-size:13.5px;color:#333}
.social{top:2782px;width:40px;height:40px;border-radius:50%;background:var(--lime)}
</style>
</head>
<body>

<!-- header -->
<header>
  <div class="abs brand"><span class="brand-dot"></span><span class="brand-name">Amber and Slate</span></div>
  <nav class="abs main-nav"><span>EXPERIENCE</span><span>ABOUT US</span><span>CONTACT US</span><span>BOOK</span><span>ALL PROPERTIES</span></nav>
</header>

<!-- hero -->
<svg class="abs" style="left:0;top:0" width="1200" height="770" viewBox="0 0 1200 770">
  <defs>
    <linearGradient id="heroFill" x1="0" y1="0" x2="0" y2="1">
      <stop offset="0" stop-color="#1c3fcf"/>
      <stop offset=".35" stop-color="#2b6ee0"/>
      <stop offset=".55" stop-color="#3e7f5a"/>
      <stop offset=".75" stop-color="#1d8fd0"/>
      <stop offset="1" stop-color="#34b7d8"/>
    </linearGradient>
  </defs>
  <path d="M0,86 C250,135 480,135 700,112 S1080,92 1200,118" fill="none" stroke="var(--lime)" stroke-width="8"/>
  <path role="img" aria-label="Photo of an Ibiza cove with pine forest, sailing boats and turquoise sea" d="M0,94 C250,143 480,143 700,120 S1080,100 1200,126 L1200,735 C1000,700 760,715 500,742 C280,760 100,730 0,672 Z" fill="url(#heroFill)"/>
  <path d="M460,748 C700,718 1000,690 1200,742 L1200,730 C1000,690 760,705 500,735 Z" fill="var(--lime)"/>
</svg>
<div class="abs serif hero-title">THE BEST WAY TO STAY IN IBIZA!</div>
<div class="abs serif hero-sub">VIVAMUS PORTTITOR PURUS NISI</div>
<div class="abs slide-arrow" style="left:66px;top:378px"><svg width="22" height="22" viewBox="0 0 22 22"><path d="M14,3 L6,11 L14,19" fill="none" stroke="#222" stroke-width="2.5"/></svg></div>
<div class="abs slide-arrow" style="left:1068px;top:378px"><svg width="22" height="22" viewBox="0 0 22 22"><path d="M8,3 L16,11 L8,19" fill="none" stroke="#222" stroke-width="2.5"/></svg></div>

<form class="abs booking-bar">
  <div class="abs field" style="left:19px;width:358px"><span>Best available rate</span><svg width="16" height="10"><path d="M1,1 L8,8 L15,1" fill="none" stroke="#666" stroke-width="1.6"/></svg></div>
  <div class="abs field" style="left:383px;width:154px"><span>Check In - Out</span><svg width="16" height="10"><path d="M1,1 L8,8 L15,1" fill="none" stroke="#666" stroke-width="1.6"/></svg></div>
  <div class="abs field" style="left:541px;width:154px;padding:0 12px"><span>2 adults&nbsp; 0 kids</span><svg width="16" height="10"><path d="M1,1 L8,8 L15,1" fill="none" stroke="#666" stroke-width="1.6"/></svg></div>
  <div class="abs book-btn">BOOK</div>
</form>

<!-- welcome -->
<section>
  <div class="abs video" role="img" aria-label="Promotional video still of a guest swimming in the sea">
    <div class="abs play"><svg width="22" height="24" viewBox="0 0 22 24"><path d="M3,1 L21,12 L3,23 Z" fill="#111"/></svg></div>
  </div>
  <h1 class="abs serif welcome-title">WELCOME TO<br><span>AMBER AND SLATE</span></h1>
  <p class="abs welcome-text">Amber and Slate Villas Ibiza is a company specialized in offering its clients accommodation in Villas on the countryside of Ibiza. Our guests enjoy the rural Ibiza, tranquility, relax, private pool, close to dream beaches and coves, the best restaurants, an unforgettable holiday for family or friends.</p>
  <div class="abs btn welcome-btn">READ MORE</div>
</section>

<!-- why -->
<svg class="abs" style="left:0;top:1190px" width="1200" height="700" viewBox="0 0 1200 700">
  <defs>
    <linearGradient id="whyFill" x1="0" y1="0" x2="1" y2="1">
      <stop offset="0" stop-color="#92bd2c"/>
      <stop offset=".5" stop-color="#4ba267"/>
      <stop offset="1" stop-color="#1e8693"/>
    </linearGradient>
  </defs>
  <path d="M0,25 C250,58 520,48 760,22 S1100,-6 1200,38 L1200,655 C1050,610 850,620 560,660 C320,690 120,680 0,600 Z" fill="url(#whyFill)"/>
</svg>
<h2 class="abs serif why-title">WHY AMBER &amp; SLATE</h2>

<div class="abs reason" style="left:74px;top:1390px">
  <svg width="100" height="62" viewBox="0 0 100 62" fill="none" stroke="#fff" stroke-width="3"><path d="M4,44 L4,32 Q6,26 16,25 L30,14 Q36,10 46,10 L66,10 Q74,10 80,18 L86,25 Q96,27 96,34 L96,44 Z"/><circle cx="24" cy="46" r="7" fill="url(#none)"/><circle cx="76" cy="46" r="7"/><path d="M36,14 L36,25 M58,11 L58,25 M30,25 L86,25"/></svg>
  SHOULD<br>RENT A CAR</div>
<div class="abs reason" style="left:292px;top:1378px">
  <svg width="80" height="74" viewBox="0 0 80 74" fill="none" stroke="#fff" stroke-width="3"><path d="M4,70 Q40,50 76,70 Z"/><path d="M40,60 Q42,35 36,14"/><path d="M36,14 Q22,6 10,16 M36,14 Q50,4 64,14 M36,14 Q28,24 22,34 M36,14 Q48,22 54,32 M36,14 Q34,6 30,2"/></svg>
  GO AROUND<br>THE ISLAND</div>
<div class="abs reason" style="left:542px;top:1375px">
  <svg width="80" height="76" viewBox="0 0 80 76" fill="none" stroke="#fff" stroke-width="3"><path d="M10,2 L62,72 M10,2 Q4,24 30,38"/><path d="M70,4 L70,20 Q70,30 60,30 L16,72 M60,4 L60,22 M52,10 L52,24"/></svg>
  EAT IN A RESTAURANT<br>ONE DAY IN FRONT<br>OF THE SEA</div>
<div class="abs reason" style="left:830px;top:1378px">
  <svg width="72" height="72" viewBox="0 0 72 72" fill="none" stroke="#fff" stroke-width="3"><path d="M28,4 A32,32 0 1 0 68,50 A28,28 0 0 1 28,4 Z"/><path d="M48,14 L48,26 M42,20 L54,20 M60,28 L60,34 M57,31 L63,31"/></svg>
  IS A NIGHT OF<br>PARTYING<br>TO THE DISCOS</div>

<div class="abs reason" style="left:74px;top:1590px">
  <svg width="76" height="64" viewBox="0 0 76 64" fill="none" stroke="#fff" stroke-width="3"><path d="M4,62 L72,62 M8,62 L8,22 M68,62 L68,22 M4,22 L72,22 L66,4 L10,4 Z"/><path d="M14,30 L38,30 L38,62 M14,30 L14,48 L30,48 M46,30 L62,30 L62,48 L46,48 Z"/></svg>
  GO<br>SHOPPING</div>
<div class="abs reason" style="left:292px;top:1583px">
  <svg width="76" height="74" viewBox="0 0 76 74" fill="none" stroke="#fff" stroke-width="3"><path d="M38,2 L72,18 L4,18 Z M4,24 L72,24 M12,28 L12,62 M28,28 L28,62 M48,28 L48,62 M64,28 L64,62 M2,66 L74,66 M2,72 L74,72"/></svg>
  VISIT THE ANCIENT<br>HERITAGE OF<br>HUMANITY</div>
<div class="abs reason" style="left:542px;top:1590px">
  <svg width="80" height="64" viewBox="0 0 80 64" fill="none" stroke="#fff" stroke-width="3"><path d="M2,18 Q12,8 22,18 T42,18 T62,18 T80,18 M2,36 Q12,26 22,36 T42,36 T62,36 T80,36 M2,54 Q12,44 22,54 T42,54 T62,54 T80,54"/></svg>
  MAKE SOME<br>AQUATIC SPORT</div>
<div class="abs reason" style="left:830px;top:1583px">
  <svg width="76" height="72" viewBox="0 0 76 72" fill="none" stroke="#fff" stroke-width="3"><path d="M20,56 L20,10 Q20,2 12,4 M52,56 L52,10 Q52,2 44,4 M20,22 L52,22 M20,38 L52,38"/><path d="M2,60 Q11,54 20,60 T38,60 T56,60 T74,60 M2,70 Q11,64 20,70 T38,70 T56,70 T74,70"/></svg>
  ENJOY THE<br>POOL</div>

<!-- testimonials -->
<section>
  <h2 class="abs serif testi-title">TESTIMONIALS</h2>
  <svg class="abs" style="left:124px;top:2034px" width="34" height="60" viewBox="0 0 34 60"><path d="M30,2 L4,30 L30,58" fill="none" stroke="#aaa" stroke-width="2"/></svg>
  <svg class="abs" style="left:1058px;top:2034px" width="34" height="60" viewBox="0 0 34 60"><path d="M4,2 L30,30 L4,58" fill="none" stroke="#aaa" stroke-width="2"/></svg>
  <div class="abs avatar" role="img" aria-label="Portrait photo of the reviewer"></div>
  <p class="abs quote"><span class="abs quote-mark" style="left:-40px;top:22px">“</span>Pellentesque faucibus Ut accumsan ultricies elit Maecenas at justo id velit placerat molestie Donec dictum lectus non odio Cras a ante vitae enim iaculis aliquam Mauris nunc quam venenatis nec euismod sit amet egestas placerat est Pellentesque habitant morbi tristique senectus et netus et malesuada fames ac turpis egestas Cras id elit <span class="quote-mark" style="position:relative;top:24px;left:4px">”</span></p>
  <div class="abs author">By Author Name</div>
</section>

<!-- experience -->
<svg class="abs" style="left:0;top:2225px" width="1200" height="550" viewBox="0 0 1200 550">
  <defs>
    <linearGradient id="expFill" x1="0" y1="0" x2="1" y2="0">
      <stop offset="0" stop-color="#1691c6"/>
      <stop offset=".5" stop-color="#22abd3"/>
      <stop offset="1" stop-color="#1897c8"/>
    </linearGradient>
    <linearGradient id="seagrass" x1="0" y1="0" x2="0" y2="1">
      <stop offset="0" stop-color="#1a7fc4"/>
      <stop offset=".45" stop-color="#2f8f6a"/>
      <stop offset=".8" stop-color="#3d9a2c"/>
      <stop offset="1" stop-color="#9fb59a"/>
    </linearGradient>
  </defs>
  <path d="M0,18 C300,50 650,20 900,8 S1150,12 1200,30" fill="none" stroke="var(--lime)" stroke-width="8"/>
  <path role="img" aria-label="Underwater background of posidonia seagrass meadow" d="M0,24 C300,56 650,26 900,14 S1150,18 1200,36 L1200,520 C1000,480 800,485 560,510 C300,540 120,530 0,480 Z" fill="url(#expFill)"/>
  <path d="M0,488 C120,536 300,546 560,518 C800,492 1000,488 1200,528 L1200,540 C1000,500 800,505 560,530 C300,556 120,546 0,500 Z" fill="var(--lime)"/>
  <circle cx="853" cy="250" r="184" fill="none" stroke="#fff" stroke-width="5"/>
  <circle role="img" aria-label="Underwater photo of green posidonia meadow" cx="853" cy="250" r="175" fill="url(#seagrass)"/>
</svg>
<h2 class="abs serif exp-title">EXPERIENCE</h2>
<p class="abs exp-text">Amber and Slate Villas Ibiza is a company specialized in offering its clients accommodation in Villas on the countryside of Ibiza. Our guests enjoy the rural Ibiza, tranquility, relax, private pool, close to dream beaches and coves, the best restaurants, an unforgettable holiday for family or friends.</p>
<div class="abs btn exp-btn">READ MORE</div>

<!-- footer -->
<footer>
  <nav class="abs foot-nav"><span>EXPERIENCE</span><span>ABOUT US</span><span>CONTACT US</span><span>BOOK</span><span>ALL PROPERTIES</span></nav>
  <div class="abs copyright">© 2019 Company Name&nbsp; All right reserved</div>
  <div class="abs social" style="left:840px"></div>
  <div class="abs social" style="left:890px"></div>
  <div class="abs social" style="left:942px"></div>
  <div class="abs social" style="left:993px"></div>
</footer>

</body>
</html>
```